Shop Front Design

We are Corwick Fusion Stores, a welding products suppliers just north of London.
We would like a banner 4.0m x 1.5m that will be placed above our building entrance to introduce our business to regular and new customers. Info we would like lister:
-Our Logo (CFS logo1)
-Core info: email address, phone number, opening hours
cfsarc@mailvane.net
07412 580 317
Monday to Friday 12:00 - 18:00
Saturday 09:00 - 12:00
-Our core services:
Welders & Consumables
Hire
Industrial Gases
Training Courses
-Our core suppliers logos. I would like to see what impact they would have on the banner
Preferred colour theme orange and grey.

```html
<!DOCTYPE html>
<html lang="en">
<head>
<meta charset="utf-8">
<title>Corwick Fusion Stores – Shop Front Banner</title>
<link href="https://fonts.googleapis.com/css2?family=Electrolize&family=Exo+2:wght@600;700&display=swap" rel="stylesheet">
<style>
  :root {
    --orange-red: #e84a1f;
    --orange: #f0821e;
    --grey: #4d4d4f;
    --ink: #1c1c1c;
    --white: #ffffff;
    --photo-dark: #0d0d0d;
  }
  * { margin: 0; padding: 0; box-sizing: border-box; }
  html, body { width: 1200px; height: 450px; overflow: hidden; background: var(--white); }
  .banner { position: relative; width: 1200px; height: 450px; overflow: hidden; font-family: "Electrolize", sans-serif; color: var(--ink); background: var(--white); }

  .brand-name {
    position: absolute; left: 21px; top: 42px;
    font-family: "Exo 2", sans-serif; font-weight: 700;
    font-size: 34px; line-height: 36px; letter-spacing: 2px;
    color: var(--orange-red); text-transform: uppercase;
  }

  .contact { position: absolute; display: flex; align-items: center; gap: 11px; font-size: 15.5px; letter-spacing: 0.4px; }
  .contact .dot { width: 37px; height: 37px; border-radius: 50%; background: var(--orange); display: flex; align-items: center; justify-content: center; flex-shrink: 0; }
  .contact-email { left: 21px; top: 139px; }
  .contact-phone { left: 247px; top: 139px; }
  .contact-hours { left: 21px; top: 204px; line-height: 21px; }

  .spark-area {
    position: absolute; left: 335px; top: 175px; width: 120px; height: 85px;
    background: radial-gradient(ellipse at 50% 100%, rgba(232,74,31,0.35), rgba(232,74,31,0) 70%);
  }

  .side-band { position: absolute; left: 479px; top: 0; width: 58px; height: 450px; background: var(--orange-red); }

  .services-title {
    position: absolute; left: 0; top: 260px; width: 510px; height: 46px;
    background: var(--orange-red); color: var(--white);
    font-size: 30px; font-weight: 400; letter-spacing: 3px; line-height: 46px; text-align: center;
  }

  .services { position: absolute; left: 0; top: 306px; width: 479px; height: 93px; display: flex; }
  .service { flex: 1; display: flex; flex-direction: column; align-items: center; justify-content: flex-start; padding-top: 10px; color: var(--white); font-family: "Exo 2", sans-serif; font-weight: 600; font-size: 10.5px; line-height: 11.5px; text-align: center; letter-spacing: 0.5px; }
  .service svg { width: 44px; height: 44px; margin-bottom: 7px; }
  .service-grey { background: var(--grey); }
  .service-orange { background: var(--orange); }

  .suppliers { position: absolute; left: 0; top: 399px; width: 479px; height: 51px; display: flex; align-items: center; padding-left: 20px; }
  .suppliers-title { font-size: 10.5px; font-weight: 400; line-height: 10.5px; letter-spacing: 0.6px; width: 70px; flex-shrink: 0; }
  .supplier-list { display: flex; gap: 8px; align-items: center; font-family: "Exo 2", sans-serif; font-weight: 700; font-size: 8px; color: var(--grey); margin-left: 2px; white-space: nowrap; }

  .photo {
    position: absolute; left: 537px; top: 0; width: 663px; height: 450px;
    background:
      radial-gradient(ellipse 180px 150px at 400px 330px, rgba(255,255,255,0.55), rgba(180,180,180,0.15) 55%, rgba(0,0,0,0) 80%),
      linear-gradient(110deg, #2b2b2b 0%, #151515 45%, var(--photo-dark) 100%);
  }
</style>
</head>
<body>
<main class="banner">
  <h1 class="brand-name">Corwick<br>Fusion Stores</h1>

  <div class="contact contact-email">
    <span class="dot">
      <svg width="20" height="20" viewBox="0 0 20 20" fill="none" stroke="#fff" stroke-width="1.6"><circle cx="10" cy="10" r="8"/><ellipse cx="10" cy="10" rx="3.5" ry="8"/><path d="M2 10h16M3.5 6h13M3.5 14h13"/></svg>
    </span>
    <span>cfsarc@mailvane.net</span>
  </div>

  <div class="contact contact-phone">
    <span class="dot">
      <svg width="18" height="18" viewBox="0 0 24 24" fill="#fff"><path d="M6.6 10.8a15.1 15.1 0 0 0 6.6 6.6l2.2-2.2a1 1 0 0 1 1-.25 11.4 11.4 0 0 0 3.6.57 1 1 0 0 1 1 1V20a1 1 0 0 1-1 1A17 17 0 0 1 3 4a1 1 0 0 1 1-1h3.5a1 1 0 0 1 1 1c0 1.25.2 2.45.57 3.57a1 1 0 0 1-.25 1z"/></svg>
    </span>
    <span>07412 580 317</span>
  </div>

  <div class="contact contact-hours">
    <span class="dot">
      <svg width="18" height="18" viewBox="0 0 20 20"><circle cx="10" cy="10" r="8.5" fill="#fff"/><path d="M10 5v5.5l3 2" fill="none" stroke="#f0821e" stroke-width="2" stroke-linecap="round"/></svg>
    </span>
    <span>Monday to Friday 12:00 - 18:00<br>Saturday 09:00 - 12:00</span>
  </div>

  <div class="spark-area" role="img" aria-label="Decorative welding spark burst"></div>

  <div class="side-band"></div>

  <h2 class="services-title">OUR CORE SERVICES</h2>

  <section class="services">
    <div class="service service-grey">
      <svg viewBox="0 0 44 44" fill="none" stroke="#fff" stroke-width="1.6" stroke-linejoin="round"><path d="M6 4v36M6 4l5 4-5 4"/><rect x="14" y="12" width="5" height="28"/><path d="M24 10h8a6 6 0 0 1 6 6v8a6 6 0 0 1-6 6h-8z"/><path d="M24 34l12 4"/></svg>
      <span>Welders &amp;<br>Consumables</span>
    </div>
    <div class="service service-orange">
      <svg viewBox="0 0 44 44" fill="none" stroke="#fff" stroke-width="1.6"><circle cx="18" cy="10" r="7"/><path d="M4 42v-10a10 10 0 0 1 10-10h8a10 10 0 0 1 10 10"/><circle cx="33" cy="33" r="8"/><path d="M29 33l3 3 5-5"/></svg>
      <span>Hire</span>
    </div>
    <div class="service service-grey">
      <svg viewBox="0 0 44 44" fill="none" stroke="#fff" stroke-width="1.6" stroke-linejoin="round"><path d="M22 4c6 7 9 11 9 16a9 9 0 0 1-18 0c0-4 3-6 5-9 1 3 2 4 4 5 0-4-1-8 0-12z"/><path d="M8 34h28M4 40h36M22 30v10"/></svg>
      <span>Industrial<br>Gases</span>
    </div>
    <div class="service service-orange">
      <svg viewBox="0 0 44 44" fill="none" stroke="#fff" stroke-width="1.6"><rect x="12" y="3" width="29" height="22" rx="1"/><circle cx="28" cy="11" r="3.5"/><path d="M22 23a6 6 0 0 1 12 0"/><circle cx="11" cy="26" r="6"/><path d="M2 42v-4a8 8 0 0 1 8-8h4a8 8 0 0 1 8 8v4z"/><path d="M22 33h8"/></svg>
      <span>Training<br>Courses</span>
    </div>
  </section>

  <section class="suppliers">
    <h3 class="suppliers-title">OUR CORE SUPPLIERS LOGOS</h3>
    <div class="supplier-list">
      <span>OSTREL</span><span>VEXLO</span><span>KYVO</span><span>TORRAK</span><span>welvio</span><span>HOBBIX</span><span>FLARN</span><span>SOLMERE</span><span>BRENZ</span><span>GRINTHO</span>
    </div>
  </section>

  <div class="photo" role="img" aria-label="Black and white photo of a welder in a helmet working on a steel frame with bright sparks flying"></div>
</main>
</body>
</html>
```